Elegant Tevani Rhum Label Design-

We are creating a Rum Distillery in the paradise island of Bora Bora which is a beautiful and exclusive honeymoon and tourist destination in the South Pacific. Our Rum label needs to reflect the beauty of Bora Bora and French Polynesia.
We would like to see designs that include the image of Mount Otemanu (* the mountain of Bora Bora) with an overwater bungalow in the image with the lagoon. We would like the label to have a turquoise color theme with either silver, white, or gold as the outline of the images. We are also open to some tropical colors as well that represent this paradise. The image needs to represent high quality class. The bottle will be sold mostly to tourist at a premium price.

On the label it needs to have Tevani Rhum as the main name-
Subheader- Light Rhum
Sub Sub header- Distilled and Bottled in Bora Bora
It needs to have 40% vol and 70cl on the label

Target Market(s)

American tourists in Bora Bora, French Polynesia

Industry/Entity Type

Rum Distillery

Colors
0094D4
00A9DD
6FCCEA
C7EBF8
E9F6FB
00AB8E
00BBA5
67D7C9
C6EFE9
E9F9F6

Requirements
Must have
• The mountain image of Otemanu and an overwater bungalow which is symbolic of Bora Bora.

```html
<!DOCTYPE html>
<html lang="en">
<head>
<meta charset="utf-8">
<title>Tevani Rhum – Light Rum Label</title>
<link rel="stylesheet" href="https://fonts.googleapis.com/css2?family=Black+Ops+One&family=IM+Fell+English&display=swap">
<style>
  :root {
    --backdrop: #e9f6fb;
    --paper: #e8e8e5;
    --ink: #3b3b3b;
    --rule: #00a9dd;
    --lagoon-deep: #0094d4;
    --lagoon-mid: #00bba5;
    --lagoon-light: #67d7c9;
  }
  * { margin: 0; padding: 0; box-sizing: border-box; }
  html, body {
    width: 801px;
    height: 1200px;
    overflow: hidden;
    background: var(--backdrop);
  }
  .canvas {
    width: 801px;
    height: 1200px;
    display: flex;
    align-items: center;
    justify-content: center;
  }
  .label {
    width: 700px;
    background: var(--paper);
    color: var(--ink);
    display: flex;
    flex-direction: column;
    box-shadow: 0 2px 10px rgba(0,0,0,0.12);
  }
  .band {
    position: relative;
    height: 240px;
    border-bottom: 4px solid var(--rule);
    display: flex;
    align-items: center;
    padding: 0 24px;
  }
  .band:last-child { border-bottom: none; height: 270px; }
  .wordmark {
    font-family: "Black Ops One", "Arial Black", sans-serif;
    line-height: 1;
    white-space: nowrap;
  }
  .band--top { justify-content: space-between; align-items: flex-end; padding-bottom: 30px; }
  .band--top .wordmark { font-size: 104px; }
  .scene-art {
    width: 190px;
    height: 190px;
    flex: none;
  }
  .band--middle { justify-content: space-between; padding-left: 60px; }
  .band--middle .wordmark { font-size: 118px; }
  .volume {
    font-family: "IM Fell English", Georgia, serif;
    font-size: 20px;
    writing-mode: vertical-rl;
    white-space: nowrap;
  }
  .band--bottom { justify-content: space-between; padding-left: 36px; }
  .band--bottom .wordmark { font-size: 118px; }
  .descriptor { flex: none; width: 270px; }
  .descriptor__type {
    font-family: "Black Ops One", "Arial Black", sans-serif;
    font-size: 34px;
    line-height: 1;
    margin-bottom: 16px;
  }
  .descriptor__origin {
    font-family: "IM Fell English", Georgia, serif;
    font-size: 26px;
    line-height: 1.25;
  }
  .descriptor__origin span { display: block; padding-left: 30px; }
</style>
</head>
<body>
<main class="canvas">
  <section class="label" aria-label="Tevani Rhum light rum label">
    <div class="band band--top">
      <div class="wordmark">TEVANI</div>
      <svg class="scene-art" role="img" aria-label="Illustration of Mount Otemanu with an overwater bungalow on the lagoon" viewBox="0 0 190 190">
        <defs>
          <linearGradient id="lagoonTone" x1="0" y1="0" x2="0" y2="1">
            <stop offset="0" stop-color="var(--lagoon-light)"/>
            <stop offset="0.6" stop-color="var(--lagoon-mid)"/>
            <stop offset="1" stop-color="var(--lagoon-deep)"/>
          </linearGradient>
        </defs>
        <rect x="0" y="0" width="190" height="190" fill="url(#lagoonTone)"/>
      </svg>
    </div>
    <div class="band band--middle">
      <div class="wordmark">TEVANI</div>
      <div class="volume">70 cl · 40% vol</div>
    </div>
    <div class="band band--bottom">
      <div class="descriptor">
        <div class="descriptor__type">LIGHT RUM</div>
        <p class="descriptor__origin">Distilled and Bottled<span>in Bora Bora</span></p>
      </div>
      <div class="wordmark">RHUM</div>
    </div>
  </section>
</main>
</body>
</html>
```